Buch-/eBook-Cover für Traumatherapeutin
Zielgruppe
Ich bin Traumatherapeutin und schreibe ein Buch zum Thema Trauma bearbeiten.
Meine Zielgruppe sucht Heilung, Genesung, Selbstliebe etc.
Aufgabenstellung
Buchcover
Bitte erstell mir ein modernes positives inspirierendes Buchcover mit dem
Titel: 'Morgenlicht NEU entdecken“
Untertitel: „Spüre den Mut der ganz in dir wohnt“
Dr. Mira Kessow
Ich hätte gerne ein modernes Buch, das entweder einen Bezug zum Thema Trauma hat oder aber einfach stylische Schriftzüge. Bin aber auch offen für andere Vorschläge.
Dunkelblau, weiß und türkis oder auch rosa mag ich ganz gerne. Wobei Dunkelblau, weiß und türkis meine Favoriten sind und mit rosa höchstens kleinere Akzente gesetzt werden sollten.
Das Buchcover soll modern sein und direkt ansprechen. Gerne eine originelle Lösung, oder etwas Besonderes, etwas das Tiefe ausdrückt, oder man mehrmals hinsehen muss um etwas zu erkennen oder etwas das mehr Interpretationsspielraum lässt.
Gerne auch viel weiß, zumindest heller und nicht zu dunkel. Stylish, aber nicht überfrachtet.
Schreib mich gerne an, wenn du Fragen hast.
Ich habe mal zwei Beispiel von Typolösungen angehängt, die ich ganz cool fände.
Ich freue mich auf deine Ideen :-)
Ganz liebe Grüße
Mira

```html
<!DOCTYPE html>
<html lang="de">
<head>
<meta charset="utf-8">
<title>Morgenlicht NEU entdecken – Dr. Mira Kessow</title>
<link rel="stylesheet" href="https://fonts.googleapis.com/css2?family=Montserrat:wght@800&family=Source+Sans+3:wght@400;500&family=Great+Vibes&display=swap">
<style>
  :root {
    --sky-deep: #6fbcd8;
    --sky-mid: #a9d8e8;
    --sky-light: #d6eef5;
    --glow: #ffffff;
    --band: rgba(255, 255, 255, 0.55);
    --title-blue: #2385ad;
    --script-turquoise: #45a9d1;
    --author-blue: #3a64a0;
    --subtitle-blue: #3d66a3;
    --petal-blue: #7aa7de;
    --petal-light: #cfe2f6;
    --skin: #f2c9ab;
  }
  html, body {
    margin: 0;
    padding: 0;
    overflow: hidden;
    background: #ffffff;
  }
  .cover {
    position: relative;
    width: 846px;
    height: 1200px;
    overflow: hidden;
    background:
      radial-gradient(ellipse 420px 360px at 400px 560px, var(--glow) 0%, rgba(255,255,255,0.85) 35%, rgba(255,255,255,0) 100%),
      radial-gradient(ellipse 500px 300px at 700px 700px, rgba(255,255,255,0.7) 0%, rgba(255,255,255,0) 100%),
      radial-gradient(ellipse 380px 260px at 80px 120px, rgba(90,170,205,0.6) 0%, rgba(90,170,205,0) 100%),
      radial-gradient(ellipse 360px 260px at 800px 250px, rgba(100,180,215,0.55) 0%, rgba(100,180,215,0) 100%),
      radial-gradient(ellipse 300px 300px at 20px 800px, rgba(90,180,215,0.5) 0%, rgba(90,180,215,0) 100%),
      linear-gradient(180deg, var(--sky-mid) 0%, var(--sky-light) 50%, var(--sky-mid) 100%);
  }
  .band {
    position: absolute;
    left: 0;
    width: 100%;
    background: var(--band);
  }
  .band--author { top: 114px; height: 54px; }
  .band--subtitle { top: 960px; height: 122px; z-index: 2; }
  .author {
    position: absolute;
    top: 114px;
    left: 0;
    width: 100%;
    height: 54px;
    margin: 0;
    line-height: 54px;
    text-align: center;
    font-family: "Source Sans 3", sans-serif;
    font-weight: 500;
    font-size: 38px;
    letter-spacing: 0.5px;
    color: var(--author-blue);
  }
  .title {
    position: absolute;
    top: 262px;
    left: 0;
    width: 100%;
    margin: 0;
    text-align: center;
    z-index: 3;
  }
  .title__line {
    display: block;
    font-family: "Montserrat", sans-serif;
    font-weight: 800;
    color: var(--title-blue);
    line-height: 1;
  }
  .title__line--first { font-size: 86px; letter-spacing: -1px; }
  .title__line--script {
    font-family: "Great Vibes", cursive;
    font-weight: 400;
    font-size: 168px;
    color: var(--script-turquoise);
    line-height: 0.9;
    margin: 4px 0 -6px;
  }
  .title__line--last { font-size: 100px; letter-spacing: -1px; }
  .illustration {
    position: absolute;
    left: 20px;
    top: 640px;
    width: 520px;
    height: 560px;
    z-index: 1;
    border-radius: 45% 55% 0 0;
    background:
      radial-gradient(ellipse 220px 170px at 300px 180px, var(--petal-blue) 0%, var(--petal-light) 60%, rgba(207,226,246,0) 100%),
      radial-gradient(ellipse 200px 380px at 210px 420px, var(--skin) 0%, rgba(242,201,171,0.5) 55%, rgba(242,201,171,0) 100%);
  }
  .subtitle {
    position: absolute;
    top: 968px;
    right: 79px;
    margin: 0;
    z-index: 3;
    text-align: right;
    font-family: "Source Sans 3", sans-serif;
    font-weight: 400;
    font-size: 42px;
    line-height: 1.2;
    color: var(--subtitle-blue);
  }
  .subtitle__script {
    font-family: "Great Vibes", cursive;
    font-size: 66px;
    color: var(--script-turquoise);
    line-height: 1;
  }
</style>
</head>
<body>
  <main class="cover">
    <div class="band band--author"></div>
    <p class="author">DR. MIRA KESSOW</p>

    <h1 class="title">
      <span class="title__line title__line--first">MORGENLICHT</span>
      <span class="title__line title__line--script">neu</span>
      <span class="title__line title__line--last">ENTDECKEN</span>
    </h1>

    <div class="illustration" role="img" aria-label="Aquarell-Illustration: eine offene Hand hält eine große hellblaue Blüte"></div>

    <div class="band band--subtitle"></div>
    <p class="subtitle">
      Spüre den <span class="subtitle__script">Mut</span><br>
      der ganz in dir wohnt
    </p>
  </main>
</body>
</html>
```